Concierge Dental / Medical Supply Ordering Business - Sleek, Efficient, Professional, Elite

www.brantonkeelmedical.com - example website.

We are a concierge supply ordering business for medical and dental that provide DSO price savings on supplies while maintaining business autonomy and independence.

We want a very simple website that looks very professional says what we do and gives a very simple method to contact us & sign up as above.

Target Market(s)

Independent Dental and Medical Practices

Industry/Entity Type

Dental and Medical - healthcare

Coding

Coded - Design and coding required

Number of Pages Required

3 page

Font styles to use
Sans Serif

Colors
0054AA
0677BA
7BADD7
CADEEF
E8F1F8

Requirements
Must have
• Simple contact page, sleek efficient design, uncomplicated.
Nice to have
• Sign up page vs just a contact page.
Should not have
• Lots of pages, hard to navigate,

```html
<!DOCTYPE html>
<html lang="en">
<head>
<meta charset="utf-8">
<title>Clearpoint Dental Supply</title>
<link rel="stylesheet" href="https://fonts.googleapis.com/css2?family=Poppins:ital,wght@0,400;0,500;0,700;0,800;1,500;1,700;1,800&display=swap">
<style>
:root{
  --blue:#0ba2e6;
  --ink:#222428;
  --text:#2c2c2c;
  --white:#ffffff;
  --icon-tint:#e8f1f8;
}
*{margin:0;padding:0;box-sizing:border-box}
html,body{width:1200px;height:2800px;overflow:hidden}
body{position:relative;font-family:'Poppins',sans-serif;color:var(--text);background:var(--white)}
.abs{position:absolute}
.btn{position:absolute;display:flex;align-items:center;justify-content:center;background:var(--blue);color:var(--white);font-weight:700;font-style:italic;font-size:16px;text-decoration:none}
.photo{position:absolute}
.accent{color:var(--blue)}

/* hero */
.hero{position:absolute;left:0;top:0;width:1200px;height:654px;background:linear-gradient(100deg,#d3d8de 0%,#c4cbd3 45%,#a9b3bd 70%,#8f9aa6 100%)}
.hero-photo{left:560px;top:180px;width:640px;height:474px;background:linear-gradient(160deg,rgba(230,235,240,.2),rgba(120,130,140,.55) 60%,rgba(170,80,90,.3))}
.brand{position:absolute;display:flex;align-items:center;gap:8px;font-weight:700;color:var(--white)}
.brand .mark{width:14px;height:14px;background:var(--blue);border-radius:50%}
.phone{left:640px;top:36px;font-size:19px;font-weight:700;font-style:italic;color:var(--ink);display:flex;align-items:center;gap:6px}
.purchase{left:948px;top:30px;width:178px;height:38px;font-size:15px;border:2px solid var(--white)}
.nav{position:absolute;left:450px;top:98px;display:flex;gap:38px;font-size:17px;font-weight:500;font-style:italic;color:var(--white)}
.nav .active{color:var(--ink);text-decoration:underline;text-underline-offset:5px}
.hero-title{position:absolute;left:73px;top:260px;font-size:50px;font-weight:800;color:#111}
.hero-text{position:absolute;left:73px;top:333px;width:580px;font-size:19px;line-height:28px;font-weight:500;color:#111}

/* welcome */
.welcome-photo{left:0;top:654px;width:520px;height:464px;background:linear-gradient(90deg,#4a4d52,#8c9096 40%,#d8dadd 85%,#ffffff)}
.welcome-title{position:absolute;left:527px;top:715px;font-size:48px;line-height:55px;font-weight:800;font-style:italic;color:var(--ink)}
.welcome-text{position:absolute;left:523px;top:845px;width:604px;font-size:13.5px;line-height:25.6px}

/* areas */
.areas-bg{position:absolute;left:0;top:1118px;width:1200px;height:636px;background:linear-gradient(90deg,#eaebee 0%,#e6e8eb 55%,#d9dde2 100%)}
.areas-title{position:absolute;left:0;width:1200px;top:1163px;text-align:center;font-size:48px;font-weight:800;font-style:italic;color:var(--ink)}
.areas-intro{position:absolute;left:70px;width:1060px;top:1230px;text-align:center;font-size:14px;line-height:26px}
.card{position:absolute;top:1320px;width:329px;height:375px;background:var(--white);text-align:center}
.card-icon{position:absolute;left:122px;top:38px;width:86px;height:86px;border-radius:50%;background:var(--icon-tint)}
.card h3{position:absolute;left:0;width:100%;top:143px;font-size:24px;font-weight:700;font-style:italic;color:var(--blue)}
.card p{position:absolute;left:28px;width:273px;top:188px;font-size:13.5px;line-height:25.6px}

/* news */
.news-title{position:absolute;left:74px;top:1805px;font-size:47px;font-weight:800;font-style:italic;color:var(--ink)}
.news-img{top:1900px;width:330px;height:208px}
.news-text{position:absolute;top:2126px;width:330px;font-size:20px;line-height:29px;font-weight:500}
.learn{position:absolute;top:2225px;font-size:12.5px;font-weight:500;color:var(--blue)}

/* quote */
.quote-bg{position:absolute;left:0;top:2307px;width:1200px;height:296px;background:linear-gradient(180deg,#3a414a,#242a31)}
.quote-title{position:absolute;left:0;width:1200px;top:2363px;text-align:center;font-size:46px;font-weight:800;font-style:italic;color:var(--white)}
.quote-text{position:absolute;left:0;width:1200px;top:2439px;text-align:center;font-size:14px;color:var(--white)}

/* footer */
.foot-nav{position:absolute;left:518px;top:2638px;display:flex;gap:34px;font-size:16px;font-weight:500;font-style:italic;color:var(--ink)}
.copy{position:absolute;right:72px;top:2692px;font-size:13.5px;color:var(--ink)}
.social{position:absolute;right:72px;top:2732px;display:flex;gap:16px}
.social span{width:22px;height:22px;border-radius:50%;background:var(--ink)}
</style>
</head>
<body>

<section class="hero">
  <div class="photo hero-photo" role="img" aria-label="Dental instruments standing in a glass cup"></div>
  <div class="brand" style="left:73px;top:100px;font-size:13px"><span class="mark"></span>Clearpoint Dental Supply</div>
  <div class="abs phone">
    <svg width="16" height="16" viewBox="0 0 24 24"><path d="M6.6 10.8a15 15 0 006.6 6.6l2.2-2.2c.3-.3.7-.4 1-.2 1.1.4 2.3.6 3.6.6.6 0 1 .4 1 1V20c0 .6-.4 1-1 1A17 17 0 013 4c0-.6.4-1 1-1h3.5c.6 0 1 .4 1 1 0 1.3.2 2.5.6 3.6.1.3 0 .7-.2 1z" fill="#222428"/></svg>
    Call Today: +1-555-014-2200
  </div>
  <a class="btn purchase">Where to Purchase</a>
  <nav class="nav"><span class="active">Home</span><span>About Us</span><span>Dental Supply</span><span>Latest News</span><span>FAQ’s</span><span>Contact Us</span></nav>
  <h1 class="hero-title">Clearpoint <span class="accent">Dental</span> Supply</h1>
  <p class="hero-text">Sed ut perspiciatis unde omnis iste natus error sit volupt atem accusantium doloremque</p>
  <a class="btn" style="left:74px;top:415px;width:166px;height:49px">Read More</a>
</section>

<section class="welcome">
  <div class="photo welcome-photo" role="img" aria-label="Row of dental hand instruments and a handpiece"></div>
  <h2 class="welcome-title">Welcome to Clearpoint<br><span class="accent">Dental</span> Supply.</h2>
  <p class="welcome-text">Sed ut perspiciatis unde omnis iste natus error sit voluptatem accusantium doloremque laudantium, totam rem aperiam, eaque ipsa quae ab illo inventore veritatis et quasi architecto beatae vitae dicta sunt explicabo. Nemo enim ipsam voluptatem quia voluptas sit aspernatur aut odit aut fugit, sed quia consequuntur magni dolores eos qui ratione voluptatem sequi nesciunt.</p>
  <a class="btn" style="left:523px;top:1002px;width:166px;height:49px">Read More</a>
</section>

<section class="areas">
  <div class="areas-bg" role="img" aria-label="Dentist at work in a bright clinic, faded"></div>
  <h2 class="areas-title">Areas of Practice</h2>
  <p class="areas-intro">Sed ut perspiciatis unde omnis iste natus error sit voluptatem accusantium doloremque laudantium, totam rem aperiam, eaque ipsa quae ab illo inventore veritatis et quasi architecto beatae vitae dicta sunt explicabo.</p>

  <div class="card" style="left:76px">
    <div class="card-icon" role="img" aria-label="Line icon for supply distribution"></div>
    <h3>Distribution</h3>
    <p>Sed ut perspiciatis unde omnis iste natus error sit voluptatem accusantium doloremque laudantium, totam rem aperiam, eaque ipsa quae ab illo in ventore veritatis et quasi architecto beatae vitae dicta sunt.</p>
  </div>
  <div class="card" style="left:438px">
    <div class="card-icon" role="img" aria-label="Line icon for dental instruments"></div>
    <h3>Dental</h3>
    <p>Sed ut perspiciatis unde omnis iste natus error sit voluptatem accusantium doloremque laudantium, totam rem aperiam, eaque ipsa quae ab illo in ventore veritatis et quasi architecto beatae vitae dicta sunt.</p>
  </div>
  <div class="card" style="left:800px">
    <div class="card-icon" role="img" aria-label="Line icon for capital equipment"></div>
    <h3>Capital Equipment</h3>
    <p>Sed ut perspiciatis unde omnis iste natus error sit voluptatem accusantium doloremque laudantium, totam rem aperiam, eaque ipsa quae ab illo in ventore veritatis et quasi architecto beatae vitae dicta sunt.</p>
  </div>
</section>

<section class="news">
  <h2 class="news-title">News Updates</h2>
  <svg class="abs" style="left:1050px;top:1818px" width="80" height="36" viewBox="0 0 80 36" fill="none" stroke-width="3"><path d="M20 2L4 18l16 16" stroke="#111"/><path d="M60 2l16 16-16 16" stroke="#0ba2e6"/></svg>
  <div class="photo news-img" style="left:74px;background:linear-gradient(135deg,#9fb6cc,#e9eef2 50%,#5a7690)" role="img" aria-label="Dental implant models"></div>
  <div class="photo news-img" style="left:436px;background:linear-gradient(180deg,#1c2a3a,#2c6a8a 60%,#4ab3c9)" role="img" aria-label="Colourful dental instruments in a row"></div>
  <div class="photo news-img" style="left:798px;background:linear-gradient(135deg,#5e8fb8,#c7dcec 50%,#2d6c94)" role="img" aria-label="Modern dental treatment room"></div>
  <p class="news-text" style="left:74px">Sed ut perspiciatis unde omnis iste natus error sit voluptatem accusantium..</p>
  <p class="news-text" style="left:436px">Sed ut perspiciatis unde omnis iste natus error sit voluptatem accusantium..</p>
  <p class="news-text" style="left:798px">Sed ut perspiciatis unde omnis iste natus error sit voluptatem accusantium..</p>
  <span class="learn" style="left:73px">Learn More</span>
  <span class="learn" style="left:435px">Learn More</span>
  <span class="learn" style="left:797px">Learn More</span>
</section>

<section class="quote">
  <div class="quote-bg" role="img" aria-label="Dental tools on a tray in dark tones"></div>
  <h2 class="quote-title">Request a Quote</h2>
  <p class="quote-text">Sed ut perspiciatis unde omnis iste natus error sit voluptatem accusantium doloremque laudantium, totam rem aperiam, eaque ipsa.</p>
  <a class="btn" style="left:517px;top:2485px;width:165px;height:49px">Contact Us</a>
</section>

<footer>
  <div class="brand" style="left:73px;top:2740px;font-size:15px;color:var(--ink)"><span class="mark"></span>Clearpoint Dental Supply</div>
  <nav class="foot-nav"><span>Home</span><span>About Us</span><span>Dental Supply</span><span>Latest News</span><span>FAQ’s</span><span>Contact Us</span></nav>
  <p class="copy">Company © 2023 Company Name All Right Reserved</p>
  <div class="social" aria-label="Social media links"><span></span><span></span><span></span><span></span><span></span></div>
</footer>

</body>
</html>
```